Security company needs a business card design

We have a logo & we provide security services specialising in the construction site industry & remote areas. We are looking for a modern design preferably hi-tech as we provide hi-end specialised security services. We do not do pubs, clubs etc. Many of our employees are ex defence force & are highly qualified in covert ops etc.

Below are details that we would like on the front of the business card (I have attached our logo)
Logo + ML 738204195 (ML is abbreviation for "Master License")
We are also members of "GRTOV" not sure if we need to put their logo on the business card or just make a reference to our membership (please advise - I have also attached their logo)

Company name: Bluegate Security Services Pty Ltd

1) Employee name: Darren Kowalczyk
Designation: Security Advisor / Director
Contact: M: 0431 582 907
e:darren@bluegatesecurityservices.com.au (500cards 1st order)
2) Employee name: Trevor Kowalczyk
Designation: Manager
Contact: M: 0476 213 564
e:trevor@bluegatesecurityservices.com.au (250cards 1st order)
3) a generic card with no employee name or designation (250cards 1st order)

Company Address: 316 Wattlebrook Rd, Coffs Harbour NSW 2450
T: +61 2 6610 4932 F: +61 2 6610 4958
E:admin@bluegatesecurityservices.com.au
www.bluegatesecurityservices.com.au

Below are details we provide which have been placed previously on the back of our business card:
Static Guards; Mobile Vehicle patrols; Alarm monitoring; 3 G CCTV Monitoring; Specialists in providing security requirements for construction sites & remote areas.
Updates

                                        Refer new pdf just uploaded

Target Market(s)

Security required for construction sites & remote areas

Industry/Entity Type

Construction

```html
<!DOCTYPE html>
<html lang="en">
<head>
<meta charset="utf-8">
<title>Bluegate Security Services – Card Back</title>
<link rel="stylesheet" href="https://fonts.googleapis.com/css2?family=Oswald:wght@600;700&display=swap">
<style>
  :root {
    --navy: #2d3183;
    --navy-deep: #2a327f;
    --white: #ffffff;
    --peach: #f7b39a;
    --red: #e5322a;
    --badge-plain: #d9dbec;
  }
  html, body {
    margin: 0;
    padding: 0;
    width: 1200px;
    height: 741px;
    overflow: hidden;
    background: var(--white);
  }
  .card {
    position: relative;
    width: 1200px;
    height: 741px;
    overflow: hidden;
    font-family: "Oswald", "Arial Narrow", sans-serif;
    background: linear-gradient(
      to bottom,
      var(--navy-deep) 0%,
      #8a8fc2 22%,
      var(--white) 39%,
      var(--white) 62%,
      var(--peach) 82%,
      var(--red) 100%
    );
  }
  .headline {
    position: absolute;
    top: 46px;
    left: 0;
    width: 100%;
    margin: 0;
    text-align: center;
    color: var(--white);
    font-weight: 700;
    font-size: 52px;
    line-height: 72px;
    letter-spacing: 3.4px;
    text-transform: uppercase;
  }
  .services {
    position: absolute;
    top: 300px;
    left: 46px;
    margin: 0;
    padding: 0;
    list-style: none;
    color: var(--navy);
    font-weight: 700;
    font-size: 45px;
    line-height: 64.8px;
    letter-spacing: 2.8px;
    text-transform: uppercase;
    white-space: nowrap;
  }
  .member-badge {
    position: absolute;
    left: 764px;
    top: 570px;
  }
  .brand-mark {
    position: absolute;
    left: 895px;
    top: 450px;
    width: 260px;
    display: flex;
    flex-direction: column;
    align-items: center;
    gap: 16px;
  }
  .brand-name {
    margin: 0;
    color: var(--navy);
    font-weight: 700;
    font-size: 38px;
    line-height: 44px;
    text-align: center;
    text-transform: uppercase;
    letter-spacing: 1px;
  }
</style>
</head>
<body>
  <main class="card">
    <h1 class="headline">Specialist Security Services<br>for Construction Sites &amp; Remote Areas</h1>

    <ul class="services">
      <li>*Static Guards *Alarm Monitoring</li>
      <li>*Mobile Vehicle Patrols *3G IP/IR Monitoring</li>
      <li>*Tactical Operations *Hunting Cams</li>
      <li>*Assett Protection *Security Briefs</li>
      <li>*Intensive Security Prescence</li>
      <li>*Security Incident Reports</li>
    </ul>

    <svg class="member-badge" width="104" height="104" viewBox="0 0 104 104" role="img" aria-label="Industry association membership badge">
      <circle cx="52" cy="52" r="50" fill="var(--badge-plain)"/>
    </svg>

    <div class="brand-mark">
      <svg width="56" height="56" viewBox="0 0 56 56" aria-hidden="true">
        <circle cx="28" cy="28" r="26" fill="var(--navy)"/>
      </svg>
      <p class="brand-name">Bluegate<br>Security<br>Services</p>
    </div>
  </main>
</body>
</html>
```